Tall Fern Roofing Business Card

Need a business card with the logo that was designed here

Contact Information for Business Card

Name, Title, Phone, Email, Website, Company name

```html
<!DOCTYPE html>
<html lang="en">
<head>
<meta charset="utf-8">
<title>Tall Fern Roofing – Business Card</title>
<link href="https://fonts.googleapis.com/css2?family=Poppins:wght@400;600;700&display=swap" rel="stylesheet">
<style>
  :root {
    --stage: #0d0d0e;
    --card: #2a2b2e;
    --card-dark: #222326;
    --edge-blue: #1f73c9;
    --brand-blue: #2a7fd4;
    --text-grey: #a9abb0;
    --rule-grey: #4a4c51;
    --emboss-light: #3a3b3f;
  }
  * { box-sizing: border-box; margin: 0; padding: 0; }
  html, body { width: 1200px; height: 820px; overflow: hidden; }
  body {
    background: radial-gradient(ellipse at 50% 45%, #1b1b1d 0%, var(--stage) 70%);
    font-family: "Poppins", sans-serif;
    position: relative;
  }
  .card {
    position: absolute;
    top: 250px;
    width: 540px;
    height: 310px;
    background: var(--card);
    border-left: 3px solid var(--edge-blue);
    border-bottom: 3px solid var(--edge-blue);
    box-shadow: 0 24px 50px rgba(0,0,0,.7);
    overflow: hidden;
  }
  .card--front { left: 40px; }
  .card--back { left: 620px; background: var(--card-dark); }

  .wordmark {
    position: absolute;
    display: flex;
    align-items: center;
    gap: 10px;
    color: var(--brand-blue);
    font-weight: 600;
    font-size: 30px;
    letter-spacing: .5px;
    white-space: nowrap;
  }
  .wordmark__square { width: 14px; height: 14px; background: var(--brand-blue); }
  .card--front .wordmark { top: 70px; left: 200px; }
  .card--back .wordmark { top: 120px; left: 60px; }

  .divider {
    position: absolute;
    left: 110px;
    right: 40px;
    top: 150px;
    height: 1px;
    background: var(--rule-grey);
  }

  .person { position: absolute; left: 46px; top: 190px; }
  .person__name { color: var(--brand-blue); font-weight: 700; font-size: 18px; text-transform: uppercase; line-height: 1.1; }
  .person__title { color: var(--text-grey); font-size: 14px; line-height: 1.3; }
  .person__rule { width: 190px; height: 1px; background: var(--rule-grey); margin: 10px 0; }

  .contact { list-style: none; }
  .contact li { display: flex; align-items: center; gap: 8px; color: var(--text-grey); font-size: 15px; line-height: 1.5; }
  .contact svg { width: 14px; height: 14px; flex: none; }

  .website { position: absolute; right: 40px; bottom: 40px; color: var(--text-grey); font-size: 14px; }
  .website__name { color: var(--brand-blue); }

  .roof-emboss {
    position: absolute;
    right: 0;
    top: 0;
    width: 230px;
    height: 100%;
    background: linear-gradient(135deg, var(--emboss-light) 0%, var(--card-dark) 60%);
  }
</style>
</head>
<body>
  <section class="card card--front" aria-label="Business card front">
    <div class="wordmark"><span class="wordmark__square"></span>Tall Fern Roofing</div>
    <div class="divider"></div>
    <div class="person">
      <p class="person__name">Marcus Hale</p>
      <p class="person__title">Managing Director</p>
      <div class="person__rule"></div>
      <ul class="contact">
        <li>
          <svg viewBox="0 0 24 24" aria-hidden="true"><path fill="var(--brand-blue)" d="M6.6 10.8a15.1 15.1 0 0 0 6.6 6.6l2.2-2.2a1 1 0 0 1 1-.25 11.4 11.4 0 0 0 3.6.6 1 1 0 0 1 1 1V20a1 1 0 0 1-1 1A17 17 0 0 1 3 4a1 1 0 0 1 1-1h3.5a1 1 0 0 1 1 1 11.4 11.4 0 0 0 .6 3.6 1 1 0 0 1-.25 1z"/></svg>
          044-555 210 347
        </li>
        <li>
          <svg viewBox="0 0 24 24" aria-hidden="true"><path fill="var(--brand-blue)" d="M2 5h20v14H2z"/><path fill="none" stroke="var(--card)" stroke-width="2" d="M2 5l10 8 10-8"/></svg>
          info@tallfern.example
        </li>
      </ul>
    </div>
    <p class="website">www.<span class="website__name">tallfern</span>.example</p>
  </section>

  <section class="card card--back" aria-label="Business card back">
    <div class="roof-emboss" role="img" aria-label="Subtle embossed roof decoration"></div>
    <div class="wordmark"><span class="wordmark__square"></span>Tall Fern Roofing</div>
  </section>
</body>
</html>
```